Young, dynamic furniture company needs a new business card design

We require a new business card design for our modern furniture company which supplies furniture and appliances to the property and development market.
Oakridge Interiors has become one of the leading furniture & appliance suppliers to the property market withing London. With over 10 years experience, we have increased our business to supply not only private landlords and managing agents, but also property developers, housing associations and local councils.
We offer not only a complete range of furniture which includes beds, wardrobes, dining sets and sofas, but also a high quality, full delivery and assembly service to help you with all our furnishing needs.

Target Market(s)

Private landlords, estate agents, letting agents, property management companies

Industry/Entity Type

Business

Contact Information for Business Card

Name,
Title,
Address,
Mobile,
Telephone,
Fax, Website, email address

Font styles to use
Sans Serif

Colors
3176b5
0555a3
85abd2
cfdeed

Requirements
Must have
• All the above information for each of our staff, along with our logo

```html
<!DOCTYPE html>
<html lang="en">
<head>
<meta charset="utf-8">
<title>Oakridge Interiors — Business Card</title>
<link rel="stylesheet" href="https://fonts.googleapis.com/css2?family=Roboto:wght@300;400;500;700&display=swap">
<style>
  :root {
    --bg: #2b2b2d;
    --blue: #3176b5;
    --blue-deep: #0555a3;
    --navy: #1e3f8c;
    --blue-soft: #85abd2;
    --blue-pale: #cfdeed;
    --ink: #2a2a2a;
    --white: #ffffff;
  }
  * { margin: 0; padding: 0; box-sizing: border-box; }
  html, body { width: 1200px; height: 950px; overflow: hidden; }
  body {
    background: var(--bg);
    font-family: "Roboto", Arial, sans-serif;
    position: relative;
  }
  .card {
    position: absolute;
    width: 640px;
    height: 366px;
    left: 280px;
    overflow: hidden;
    box-shadow: 0 12px 30px rgba(0,0,0,0.45);
  }
  .brand-row { display: inline-flex; align-items: center; gap: 12px; white-space: nowrap; }
  .brand-mark { width: 22px; height: 22px; background: currentColor; flex: none; }
  .brand-name {
    font-size: 34px; font-weight: 500; letter-spacing: 1px; text-transform: uppercase;
  }
  .brand-tagline {
    font-size: 12px; font-weight: 400; letter-spacing: 2px; text-transform: uppercase;
    margin-top: 6px;
  }
  /* Back side */
  .card-back {
    top: 80px;
    background: linear-gradient(135deg, #3a82c2 0%, var(--blue) 55%, #2b6aa8 100%);
    color: var(--white);
    text-align: center;
  }
  .card-back .brand { position: absolute; left: 0; right: 0; top: 128px; }
  .card-back .web {
    position: absolute; left: 0; right: 0; bottom: 82px;
    font-size: 14px; letter-spacing: 5px; font-weight: 300;
  }
  /* Front side */
  .card-front { top: 504px; background: var(--white); }
  .card-front svg.shapes { position: absolute; inset: 0; }
  .card-front .brand {
    position: absolute; left: 20px; width: 400px; top: 98px; text-align: center; color: var(--ink);
  }
  .card-front .brand-row { gap: 10px; }
  .card-front .brand-name { font-size: 24px; color: var(--ink); }
  .card-front .brand-mark { width: 16px; height: 16px; background: var(--navy); }
  .card-front .brand-tagline { font-size: 10px; color: var(--ink); margin-top: 4px; }
  .person {
    position: absolute; right: 30px; top: 130px; text-align: right; color: var(--white);
  }
  .person-name { font-size: 20px; font-weight: 700; text-transform: uppercase; letter-spacing: .5px; }
  .person-title { font-size: 13px; text-transform: uppercase; letter-spacing: 1px; margin-bottom: 8px; }
  .person-address { font-size: 14px; line-height: 1.35; font-weight: 300; }
  .contacts {
    position: absolute; left: 30px; top: 256px; list-style: none; color: var(--white);
    font-size: 14px; font-weight: 300;
  }
  .contacts li { display: flex; align-items: center; gap: 10px; height: 24px; }
  .contacts svg { width: 14px; height: 14px; fill: var(--white); flex: none; }
</style>
</head>
<body>

  <section class="card card-back" aria-label="Card back">
    <div class="brand">
      <div class="brand-row">
        <span class="brand-mark"></span>
        <span class="brand-name">Oakridge Interiors</span>
      </div>
      <div class="brand-tagline">Trade Furniture Solutions</div>
    </div>
    <div class="web">www.oakridgeint.com</div>
  </section>

  <section class="card card-front" aria-label="Card front">
    <svg class="shapes" viewBox="0 0 640 366" preserveAspectRatio="none" aria-hidden="true">
      <defs>
        <linearGradient id="panelBlue" x1="0" y1="0" x2="1" y2="1">
          <stop offset="0" stop-color="#3a82c2"/>
          <stop offset="1" stop-color="#2b6aa8"/>
        </linearGradient>
      </defs>
      <polygon points="455,105 640,105 640,330 330,235" fill="url(#panelBlue)"/>
      <polygon points="0,235 330,235 640,330 640,366 0,366" fill="var(--navy)"/>
      <line x1="330" y1="235" x2="640" y2="330" stroke="#ffffff" stroke-width="2"/>
    </svg>

    <div class="brand">
      <div class="brand-row">
        <span class="brand-mark"></span>
        <span class="brand-name">Oakridge Interiors</span>
      </div>
      <div class="brand-tagline">Trade Furniture Solutions</div>
    </div>

    <div class="person">
      <div class="person-name">Mark Ellison</div>
      <div class="person-title">President</div>
      <div class="person-address">2170 Harrow Lane<br>Millbrook, NY 12545</div>
    </div>

    <ul class="contacts">
      <li>
        <svg viewBox="0 0 16 16"><path d="M2 4c0-1 1-2 2-2h8c1 0 2 1 2 2v1h-3V4H5v1H2zM4 7h8l2 7H2z"/></svg>
        555 0142 7781
      </li>
      <li>
        <svg viewBox="0 0 16 16"><path d="M5 1h6a1 1 0 0 1 1 1v12a1 1 0 0 1-1 1H5a1 1 0 0 1-1-1V2a1 1 0 0 1 1-1zm1 2v9h4V3z"/></svg>
        555 0198 3364
      </li>
      <li>
        <svg viewBox="0 0 16 16"><path d="M4 1h6v4H4zM2 6h12v6h-2v3H4v-3H2zm4 5v2h4v-2z"/></svg>
        555 0176 2209
      </li>
      <li>
        <svg viewBox="0 0 16 16"><path d="M1 3h14v10H1zm1.5 1.5L8 9l5.5-4.5z"/></svg>
        mark@oakridgeint.com
      </li>
    </ul>
  </section>

</body>
</html>
```